Travel Agency Website - Simple General

Need a 7 page simple design that is pretty repetitive. Need to be able to load quickly that is SEO optimized. Trying to give ideas on what they can do, be personal as we are local, but at the same time come across as professional and get information easily with little burden.

- Landing Page
- Brimwell Vacations Page
- Family Trips
- Road Trips from Texas
- Other Destinations
- About Us Page
- Contact Us Page

Target Market(s)

Families

Coding

Coded - Design and coding required

Number of Pages Required

5+ page

Colors

Designer to choose colors to be used in the design.

Requirements
Must have
• Like it to flow easily with our logo. Use that for colors, etc.

```html
<!DOCTYPE html>
<html lang="en">
<head>
<meta charset="utf-8">
<title>Contact | Meander &amp; Roam Travel Co.</title>
<link href="https://fonts.googleapis.com/css2?family=Barlow+Condensed:wght@500;600&family=Outfit:wght@300;400;500&display=swap" rel="stylesheet">
<style>
:root{
  --ink:#0b3f4c;
  --teal:#1f7b7c;
  --panel:rgba(38,128,130,.86);
  --gold:#c4954a;
  --white:#ffffff;
  --muted:#4a5b60;
  --sky-top:#cfdde3;
  --sky-mid:#e3e9e3;
  --ground:#e6e6dc;
}
*{box-sizing:border-box;margin:0;padding:0}
html,body{width:1200px;height:889px;overflow:hidden}
body{font-family:"Outfit",sans-serif;color:var(--ink);position:relative;background:var(--ground)}
.hero-scene{position:absolute;inset:0 0 64px 0;
  background:
   radial-gradient(ellipse 280px 340px at 830px 520px,rgba(70,110,110,.35),transparent 70%),
   linear-gradient(180deg,var(--sky-top) 0%,var(--sky-mid) 45%,#d9ddd2 70%,#dcdccd 100%)}
.footer-band{position:absolute;left:0;right:0;bottom:0;height:64px;background:var(--ground)}
.display{font-family:"Barlow Condensed",sans-serif;font-weight:600;letter-spacing:-.01em}
.brand{position:absolute;left:126px;top:40px;display:flex;align-items:center;gap:8px;font-family:"Outfit",sans-serif;font-weight:500;font-size:17px;color:var(--ink)}
.brand-dot{width:14px;height:14px;border-radius:50%;background:var(--gold)}
.nav{position:absolute;top:50px;right:125px;display:flex;gap:24.5px;font-size:10.5px;color:var(--ink)}
.page-title{position:absolute;top:160px;left:0;width:1200px;text-align:center;font-size:56px;line-height:1;color:var(--ink)}
.contact-info{position:absolute;left:201px;top:348px;width:300px}
.contact-info h2{font-size:27px;line-height:1;color:var(--ink)}
.contact-info .lead{font-size:15px;margin-top:7px;color:var(--ink)}
.contact-info .note{font-size:10px;color:var(--muted);font-weight:300;margin-top:8px}
.contact-info h3{font-size:15.5px;color:var(--teal);font-weight:500;margin-top:19px}
.detail{display:flex;align-items:center;gap:9px;margin-top:10px}
.detail:first-of-type{margin-top:15px}
.icon{width:40px;height:40px;border-radius:50%;background:var(--gold);display:flex;align-items:center;justify-content:center;flex:none}
.detail b{display:block;font-size:9.5px;font-weight:500}
.detail span{font-size:13px;font-weight:400}
.follow{font-size:15.5px;color:var(--teal);font-weight:500;margin-top:20px}
.socials{display:flex;gap:42px;margin-top:13px}
.social{display:flex;align-items:center;gap:6px;font-size:10.5px;text-decoration:underline;color:var(--ink)}
.social i{width:27px;height:27px;border-radius:50%;background:var(--gold);display:block}
.reply{font-size:10px;color:var(--muted);font-weight:300;margin-top:17px}
.message-form{position:absolute;left:557px;top:294px;width:437px;height:445px;border-radius:19px;background:var(--panel);border:1px solid rgba(15,70,72,.5);padding:24px 37px 0}
.message-form h2{text-align:center;color:var(--white);font-size:28px;line-height:1}
.grid{display:grid;grid-template-columns:176px 176px;column-gap:10px;margin-top:24px}
.field label{display:block;color:var(--white);font-family:"Barlow Condensed",sans-serif;font-weight:500;font-size:11.5px;margin-bottom:5px}
.field .box{background:var(--white);border-radius:5px;height:35px}
.field.row2{margin-top:13px}
.field.wide{grid-column:1/3;margin-top:13px}
.field.wide .box{height:99px}
.send{grid-column:1/3;margin-top:9px;height:35px;border-radius:5px;background:var(--gold);color:var(--white);font-family:"Barlow Condensed",sans-serif;font-weight:500;font-size:12px;display:flex;align-items:center;justify-content:center}
</style>
</head>
<body>
<div class="hero-scene" role="img" aria-label="Traveler with backpack raising binoculars on a grassy hilltop above hazy mountains"></div>
<div class="footer-band"></div>

<div class="brand"><span class="brand-dot"></span>Meander &amp; Roam</div>
<nav class="nav">
  <span>Home</span><span>Brimwell Vacations</span><span>Family Trips</span><span>Texas Road Trips</span><span>Other Destinations</span><span>About Us</span><span>Contact</span>
</nav>

<h1 class="page-title display">Meander &amp; Roam</h1>

<section class="contact-info">
  <h2 class="display">Contact Us</h2>
  <p class="lead display">We'd love to hear form you!</p>
  <p class="note">fill out the form or use our details to connect.</p>
  <h3 class="display">Contact information</h3>
  <div class="detail">
    <div class="icon"><svg width="14" height="14" viewBox="0 0 24 24"><path fill="#fff" d="M6.6 10.8a15 15 0 0 0 6.6 6.6l2.2-2.2c.3-.3.7-.4 1-.2 1.1.4 2.3.6 3.6.6.6 0 1 .4 1 1V20c0 .6-.4 1-1 1A17 17 0 0 1 3 4c0-.6.4-1 1-1h3.5c.6 0 1 .4 1 1 0 1.3.2 2.5.6 3.6.1.3 0 .7-.2 1z"/></svg></div>
    <div><b>Call Us:</b><span>555.014.2290</span></div>
  </div>
  <div class="detail">
    <div class="icon"><svg width="15" height="12" viewBox="0 0 24 18"><rect x="1" y="1" width="22" height="16" rx="2" fill="#fff"/><path d="M2 3l10 7 10-7" fill="none" stroke="#c4954a" stroke-width="2"/></svg></div>
    <div><b>Email Address:</b><span>hello@meanderandroam.com</span></div>
  </div>
  <p class="follow display">Follow Us &amp; Jion oour adventure!</p>
  <div class="socials">
    <span class="social"><i></i>Lumenly</span>
    <span class="social"><i></i>Picroll</span>
  </div>
  <p class="reply">We respond within 24–48 hours to all inquiries.</p>
</section>

<section class="message-form">
  <h2 class="display">Send Us a Message</h2>
  <div class="grid">
    <div class="field"><label>First Name*</label><div class="box"></div></div>
    <div class="field"><label>Last Name*</label><div class="box"></div></div>
    <div class="field row2"><label>Email Address*</label><div class="box"></div></div>
    <div class="field row2"><label>Phone Number*</label><div class="box"></div></div>
    <div class="field wide"><label>Any details you want us to know?</label><div class="box"></div></div>
    <div class="send">SENT MESSAGE</div>
  </div>
</section>
</body>
</html>
```